Letterhead Design for Law Firm

**Edit: I have added the photo of a bottom that I like.

------
We are looking for a re-design of our new letterhead. The letterhead is for a law firm and will be used for digital and traditionally printed correspondence.

Here are some suggestions:

- Please use colours are #8ec900 and simple black.
- Please do not use any type of "waves" at the bottom of the page. This is not in style at all.
- Please stay modern yet conservative.
- Please use font Segoe UI Light or similar if you can
- Avoid clipart or illustrations.
- Utilize ample white space in the layout so the design looks clean and information is easy to read at a glance. Don't overcrowd the letterhead.
- Make sure the letterhead design is consistent with our brand identity (see corvelith.ca)
-Please, no black headers or footers.

I am attaching my current letterhead and signature for your convenience.

Remember, the letterhead is an extension of our professional identity. We are a successful firm and trial lawyers who correspond with insurers, judges, lawyers, courts, clients, etc. Make it new, modern, attractive, yet powerful and conservative.

It needs to be easily printable. I would like the bleed removed in print so the black bar the bottom crosses the page (but the text is not near the edges)
Updates

Low design quality

Target Market(s)

Clients, Government Offices, Judiciary, Lawyers, Insurance Companies, Colleagues.

Industry/Entity Type

Law

Other font styles liked:
• Segoe UI LIght, Calibri Light,

Colors
00AB8E
00BBA5
67D7C9
C6EFE9
E9F9F6

Requirements
Must have
• Everything that is on the letterhead now.
Nice to have
• Cutting Edge design, yet conservative.
Should not have
• law firm cliche design, images,

```html
<!DOCTYPE html>
<html lang="en">
<head>
<meta charset="utf-8">
<title>Varenne Personal Injury Lawyers – Letterhead</title>
<link href="https://fonts.googleapis.com/css2?family=Carlito:wght@400;700&display=swap" rel="stylesheet">
<style>
  :root {
    --brand-green: #8ec900;
    --ink: #111111;
    --body-ink: #2a2a2a;
    --paper: #ffffff;
    --backdrop: #e9e9e6;
  }
  * { margin: 0; padding: 0; box-sizing: border-box; }
  html, body {
    width: 1200px; height: 1141px; overflow: hidden;
    background: var(--backdrop);
    font-family: "Carlito", "Calibri", sans-serif;
    color: var(--body-ink);
  }
  .letterhead {
    position: absolute; left: 210px; top: 20px;
    width: 779px; height: 1101px;
    background: var(--paper);
    box-shadow: 0 2px 10px rgba(0,0,0,0.15);
  }
  .accent-bar {
    position: absolute; left: 0; top: 0; bottom: 0; width: 11px;
    background: var(--brand-green);
  }
  .abs { position: absolute; }
  .firm-name {
    left: 53px; top: 56px; width: 250px;
    color: var(--ink); font-weight: 400; text-align: center;
  }
  .firm-name .name-main { display: block; font-size: 62px; line-height: 56px; letter-spacing: 1px; }
  .firm-name .name-sub { display: block; font-size: 15px; letter-spacing: 1.6px; margin-top: 6px; }
  .practice-list {
    right: calc(779px - 552px); top: 50px;
    text-align: right; font-size: 11.5px; line-height: 13.4px; color: var(--body-ink);
  }
  .practice-list .label { color: var(--brand-green); font-weight: 700; }
  .header-divider {
    left: 568px; top: 41px; width: 1.5px; height: 100px; background: var(--brand-green);
  }
  .contact-block { left: 585px; top: 39px; font-size: 10.5px; line-height: 13px; color: var(--body-ink); }
  .contact-row { position: relative; padding-left: 12px; }
  .contact-row svg { position: absolute; left: 0; top: 2px; width: 8px; height: 9px; fill: var(--brand-green); }
  .contact-row.gap { margin-top: 3px; }
  .file-clerk { margin-top: 7px; }
  .file-clerk .label { color: var(--brand-green); font-weight: 700; }
  .letter-body { font-size: 14px; line-height: 18.5px; color: var(--body-ink); }
  .letter-body .strong-line { color: var(--ink); }
  .subject-rule {
    left: 53px; top: 566px; width: 674px; height: 2px; background: var(--brand-green);
  }
  .signature-area {
    left: 53px; top: 847px; width: 210px; height: 50px;
    background: linear-gradient(90deg, #f4f4f4, #e6e6e6);
  }
</style>
</head>
<body>
  <main class="letterhead">
    <div class="accent-bar"></div>

    <div class="abs firm-name">
      <span class="name-main">VARENNE</span>
      <span class="name-sub">PERSONAL INJURY LAWYERS</span>
    </div>

    <div class="abs practice-list">
      <div class="label">Practice Restricted</div>
      <div>Serious Personal Injury</div>
      <div>Wrongful Death Litigation</div>
      <div>Long-Term Disability Litigation</div>
      <div>Wrongful Dismissal Litigation</div>
      <div>Employee Terminations</div>
    </div>

    <div class="abs header-divider"></div>

    <div class="abs contact-block">
      <div class="contact-row">
        <svg viewBox="0 0 8 10"><path d="M4 0C1.8 0 0 1.7 0 3.8 0 6.5 4 10 4 10s4-3.5 4-6.2C8 1.7 6.2 0 4 0zm0 5.3a1.5 1.5 0 1 1 0-3 1.5 1.5 0 0 1 0 3z"/></svg>
        48 Arden Street E., Suite 1210<br>Brantwood, ON&nbsp; L4R 2B7
      </div>
      <div class="contact-row gap">
        <svg viewBox="0 0 10 9"><path d="M0 3C1.5 1 3.5 0.5 5 0.5S8.5 1 10 3L8.5 4 7 3V2.3C5.7 2 4.3 2 3 2.3V3L1.5 4zM2 5h6l1 4H1z"/></svg>
        905-555-0142
      </div>
      <div class="contact-row">
        <svg viewBox="0 0 10 9"><path d="M2 0h5v3H2zM0 3.5h10V9H0zm2 1.5v1h2V5zm4 0v1h2V5zM2 7v1h2V7zm4 0v1h2V7z"/></svg>
        905-555-0187
      </div>
      <div class="contact-row">
        <svg viewBox="0 0 10 8"><path d="M0 1l5 3.2L10 1V0H0zM0 2.3V8h10V2.3L5 5.5z"/></svg>
        nadia@corvelith.ca
      </div>
      <div class="contact-row">
        <svg viewBox="0 0 10 10"><circle cx="5" cy="5" r="4.5"/><path d="M5 .5v9M.5 5h9" stroke="#fff" stroke-width="0.9"/></svg>
        www.CORVELITH.ca
      </div>
      <div class="file-clerk"><span class="label">File Clerk:</span> Nadia Quillfort</div>
    </div>

    <div class="abs letter-body strong-line" style="left:53px; top:188px;">Without Prejudice</div>
    <div class="abs letter-body" style="left:53px; top:225px;">March 13, 2024</div>
    <div class="abs letter-body strong-line" style="left:53px; top:262px;">By Email</div>

    <div class="abs letter-body" style="left:53px; top:316px;">
      Northvale Insurance Company<br>
      Claims Litigation Department<br>
      240 Orchard Park Road<br>
      P.O. Box 3100<br>
      Elmridge, ON&nbsp;&nbsp; N3K 5T2
    </div>

    <div class="abs letter-body" style="left:53px; top:426px;">Attention:&nbsp; Mr. Dorian Kells</div>
    <div class="abs letter-body" style="left:53px; top:463px;">Mr. Kells:</div>

    <div class="abs letter-body strong-line" style="left:53px; top:500px;">Re:</div>
    <div class="abs letter-body strong-line" style="left:221px; top:501px;">
      Marsh v. Oberlin et al.<br>
      DOL:&nbsp; September 12, 2019<br>
      Pre-Mediation Settlement Proposal – March 13th, 2024
    </div>

    <div class="abs subject-rule"></div>

    <div class="abs letter-body" style="left:53px; top:796px; line-height:17px;">
      Yours very truly,<br>
      VARENNE PERSONAL INJURY LAWYERS
    </div>

    <div class="abs signature-area" role="img" aria-label="Handwritten signature of Paul D. Varenne"></div>

    <div class="abs letter-body" style="left:53px; top:920px; line-height:21px;">
      Paul D. Varenne<br>
      Varenne Law Professional Corporation<br>
      /nq<br>
      Encl.
    </div>
  </main>
</body>
</html>
```